I need a logo design for a new company based in Tucson called "Mindtrail Lee Corwin". I am a psychotherapist that specializes in clinical psychology with athletes and performers. The final design should incorporate the psychology symbol as a watermark. The logo should convey movement and fluidity. "Mindtrail" is a bit of a play on words combining psychology (head) with sports (coach). Other design interests include mid-century, Harold Ames Whitby. I will want to use the logo for business cards, letterhead and marketing brochures. I will put together a website at a later date. I am attaching a file with some pertinent information for the business card. Thank you.
Lee Corwin
mindtrailleecorwin@quillpost.net

Thank you all for the submissions so far.  I have submitted an additional file with a draft of a new design idea.  Since "mindtrail" is a bit of a play on words, I would like to see something with the two "H's" look something like quotation marks.  If the psychology logo is to be included at all, it needs to be less prominent.     Thank you all.  Lee                               

Target Market(s)

1) Adolescent and adult athletes and performers who are looking to increase their level of performance (Sport and Performance Psychology)
2) Adult psychotherapy patients (Clinical psychology)

Industry/Entity Type

Marketing

Colors

Designer to choose colors to be used in the design.

Requirements
Must have
• 1) Since "mindtrail" is a bit of a play on words, The "H's" need to be in a font that looks somewhat like quotation marks.

Nice to have
• Logo on one side. All other info on the backside?

```html
<!DOCTYPE html>
<html lang="en">
<head>
<meta charset="utf-8">
<title>Mindtrail – Business Card</title>
<link rel="stylesheet" href="https://fonts.googleapis.com/css2?family=Alegreya:wght@500&family=Lato:wght@400;700&display=swap">
<style>
  :root {
    --page-bg: #d9d8d6;
    --card-bg: #525252;
    --card-edge: #3a3a3a;
    --teal: #7bbcb0;
  }
  * { box-sizing: border-box; margin: 0; padding: 0; }
  html, body {
    width: 1200px;
    height: 1000px;
    overflow: hidden;
    background: var(--page-bg);
  }
  .canvas {
    position: relative;
    width: 1200px;
    height: 1000px;
  }
  .card {
    position: absolute;
    width: 630px;
    height: 370px;
    background: var(--card-bg);
    border-radius: 16px;
    box-shadow: 0 6px 0 var(--card-edge), 0 14px 24px rgba(0,0,0,0.18);
    color: var(--teal);
  }
  .card--front {
    left: 480px;
    top: 70px;
    display: flex;
    flex-direction: column;
    align-items: center;
    justify-content: center;
  }
  .card--back {
    left: 90px;
    top: 540px;
    text-align: center;
    padding-top: 58px;
  }
  .brand-name {
    font-family: "Lato", sans-serif;
    font-weight: 700;
    font-size: 84px;
    letter-spacing: 3px;
    text-transform: uppercase;
    line-height: 1;
  }
  .brand-tagline {
    margin-top: 16px;
    font-family: "Lato", sans-serif;
    font-weight: 400;
    font-size: 24px;
    letter-spacing: 2px;
    text-transform: uppercase;
  }
  .holder-name {
    font-family: "Alegreya", serif;
    font-weight: 500;
    font-size: 44px;
    letter-spacing: 1px;
    line-height: 1.1;
  }
  .holder-title {
    font-family: "Lato", sans-serif;
    font-size: 20px;
    margin-top: 4px;
  }
  .contact-list {
    list-style: none;
    margin-top: 42px;
    font-family: "Lato", sans-serif;
    font-size: 21px;
    line-height: 1.55;
  }
</style>
</head>
<body>
<main class="canvas">
  <section class="card card--front" aria-label="Card front">
    <h1 class="brand-name">Mindtrail</h1>
    <p class="brand-tagline">Clinical &amp; Performance Psychology</p>
  </section>

  <section class="card card--back" aria-label="Card back">
    <h2 class="holder-name">Lee H. Corwin, MA, LLC</h2>
    <p class="holder-title">Licensed Professional Counselor</p>
    <ul class="contact-list">
      <li>Fax: 520.555.0147</li>
      <li>Mobile: 520.555.0182</li>
      <li>Email: mindtrailleecorwin@quillpost.net</li>
      <li>Address: 4150 East Sabino Way #210 Tucson, AZ 85718</li>
    </ul>
  </section>
</main>
</body>
</html>
```